Wordpress Powered Website. Outstanding Design Required. Using Morvenic Theme

Designers will not need to create anything other than the home page but there are some design elements on the home page which also need to be factored in: 6 product place holders and 2-3 slides for a slideshow (with images I provide).

Designers will need to familiarise themselves with the Morvenic theme to make sure that their design will work within the theme.

The winning designer will set up all the pages and navigation in place. This includes social media icons, favicon, widgets, etc. In other words, the home page needs to be designed and coded and the other preset theme pages need to be organised in a way that we can start using the website on completion of the job.

Most of the designs I had last time were too colourful. This needs to be subtle not in your face.

Background to the business/website:
Ridgeway Banners is a new Australian venture which will sell large format printed banners and other signage. The market is very competitive so it is important to stand out visually and to have a website which is clean, easy to navigate and easy to order. It will be a combination of online sales and assisted sales but all sales enquiries will come from the website.

As our business is focused on presentation it is vital to have excellent design.
Purchased theme is Morvenic. Only this theme is to be used.

1. A home page using all the preset features of the Morvenic theme - it will just be basically taking my wireframe and inputting it to the live theme.
2. A three slide slideshow, ideally with an edited video. The static image slides can be provided by me during the handover. Placeholder for now.
Similar to this one: http://thecedarhollow.example.au/

Attached is the logo which must be utilised, although it could also sit on a dark background. There is our mascot as well which can be used but does not have to be included.

Target Market(s)

Primarily B2B (business to business)
Main industries will be Construction, Retail, Community, Events & Trade Shows

Industry/Entity Type

Printing

Coding

Coded - Design and coding required

Font styles to use
Sans Serif

Requirements
Must have
• Must have the design files made to web pages within the Wordpress environment.
Nice to have
• Clean design. Stand out from competitors based on design.
Should not have
• Should not look like any competitor

```html
<!DOCTYPE html>
<html lang="en">
<head>
<meta charset="utf-8">
<title>Ridgeway Banners — Home</title>
<link href="https://fonts.googleapis.com/css2?family=Lato:ital,wght@0,400;0,700;0,900;1,400&display=swap" rel="stylesheet">
<style>
:root{
  --red:#d0121b;
  --red-dark:#a80d14;
  --orange:#f26522;
  --ink:#333333;
  --heading:#4a4a4a;
  --muted:#777777;
  --line:#dddddd;
  --grey-bg:#f0f0f0;
  --card-bg:#ececec;
  --dark:#2b2b2b;
  --footer:#353535;
  --white:#ffffff;
  --icon-grey:#666666;
  --blue:#2a7fc1;
  --green:#6abf2e;
}
*{box-sizing:border-box;margin:0;padding:0}
html,body{width:1200px;height:3614px;overflow:hidden}
body{font-family:'Lato',Arial,sans-serif;color:var(--ink);background:var(--white);position:relative}
.section{position:absolute;left:0;width:1200px}
.abs{position:absolute}
.center{text-align:center}
.section-title{position:absolute;left:0;width:1200px;text-align:center;font-weight:700;color:var(--heading);font-size:40px;letter-spacing:.5px}

/* hero + header */
.hero{top:0;height:622px;background:linear-gradient(135deg,#6d5a48 0%,#9a8a78 30%,#d8d3cb 55%,#8e8171 80%,#4e4338 100%)}
.hero-shade{top:0;left:0;width:1200px;height:140px;background:linear-gradient(rgba(0,0,0,.55),rgba(0,0,0,0))}
.topbar{top:10px;left:111px;width:978px;height:24px;color:var(--white);font-size:11px;font-weight:700;display:flex;align-items:center}
.social{display:flex;gap:10px;margin-right:18px}
.social span{width:12px;height:12px;border-radius:50%;background:var(--white);opacity:.85}
.topbar .right{margin-left:auto;display:flex;gap:22px;align-items:center}
.search-box{width:24px;height:24px;background:rgba(0,0,0,.6);display:flex;align-items:center;justify-content:center}
.logo{top:52px;left:111px;font-weight:900;font-size:22px;color:var(--white);letter-spacing:.5px;line-height:1}
.logo small{display:block;font-size:10px;font-weight:900;letter-spacing:3px;margin-top:3px}
.nav{top:58px;left:316px;display:flex;gap:6px;font-size:14px;font-weight:700;color:var(--white)}
.nav a{padding:6px 8px;color:inherit;text-decoration:none}
.nav a.active{background:var(--red);border-radius:3px}
.cart{top:64px;left:920px;color:var(--white);font-size:11px;font-weight:700;display:flex;gap:8px;align-items:center}
.cart .count{width:14px;height:14px;border-radius:50%;background:var(--red);font-size:9px;display:flex;align-items:center;justify-content:center}
.quote-badge{top:50px;left:1026px;width:60px;height:50px;background:var(--orange);border-radius:4px 4px 4px 4px;color:var(--white);font-size:12px;font-weight:900;text-align:center;line-height:14px;padding-top:10px}
.promo{top:523px;left:200px;width:800px;height:171px;background:var(--red);color:var(--white)}
.promo h2{position:absolute;left:36px;top:30px;font-size:31px;font-weight:700}
.promo p{position:absolute;left:36px;top:80px;font-size:19px;line-height:30px}
.promo .btn-outline{position:absolute;left:575px;top:54px;width:187px;height:66px;border:2px solid var(--white);border-radius:6px;font-size:19px;display:flex;align-items:center;justify-content:center}

/* about */
.about{top:622px;height:438px}
.about .sub{position:absolute;top:207px;left:0;width:1200px;text-align:center;font-style:italic;font-size:16px;color:#555}
.about .body{position:absolute;top:241px;left:165px;width:870px;text-align:center;font-size:12.5px;line-height:25px;color:var(--muted)}
.btn-red{background:var(--red);color:var(--white);font-weight:900;font-size:13px;border-radius:4px;display:flex;align-items:center;justify-content:center}

/* services */
.services{top:1060px;height:463px;background:var(--grey-bg)}
.service-card{top:130px;width:294px;height:275px;background:var(--card-bg);padding:30px 26px}
.service-card.active{background:var(--white);border:1px solid var(--line);box-shadow:0 2px 6px rgba(0,0,0,.08)}
.service-card h3{font-weight:400;font-size:25px;color:var(--ink);margin-top:22px}
.service-card p{font-size:12px;line-height:21px;color:var(--muted);margin-top:14px}

/* projects */
.projects{top:1523px;height:713px}
.filters{top:145px;left:0;width:1200px;display:flex;justify-content:center;gap:20px}
.filters span{height:40px;border:1px solid #cfcfcf;border-radius:4px;font-size:11px;font-weight:700;color:#555;display:flex;align-items:center;justify-content:center;padding:0 26px}
.filters span.active{background:var(--red);border-color:var(--red);color:var(--white);padding:0 30px}
.tile{border-radius:8px;overflow:hidden}
.tile .plus{position:absolute;left:50%;top:50%;width:54px;height:54px;margin:-27px 0 0 -27px;border:2px solid var(--white);border-radius:50%;background:rgba(255,255,255,.2)}
.caption{position:absolute;left:0;bottom:16px;width:425px;height:128px;background:var(--red);color:var(--white);padding:16px 20px}
.caption h4{font-size:22px;font-weight:700}
.caption p{font-size:12px;line-height:20px;margin-top:8px}

/* features */
.features{top:2236px;height:444px;background:#f5f5f5}
.features .section-title{font-size:27px;top:52px}
.feature-card{top:126px;width:196px;height:248px;background:var(--white);border:1px solid #cfcfcf;border-radius:6px;text-align:center;padding-top:30px}
.feature-card h5{font-size:17px;font-weight:400;color:var(--ink);line-height:24px;margin-top:18px}
.feature-card p{font-size:12px;line-height:21px;color:var(--muted);margin-top:8px}

/* testimonials */
.testimonials{top:2680px;height:525px;background:linear-gradient(180deg,#3c3c3c 0%,#555 45%,#3a3a3a 100%)}
.testimonials .section-title{color:var(--white);top:65px;font-size:34px}
.avatar{top:148px;left:544px;width:112px;height:112px;border-radius:50%;border:5px solid rgba(255,255,255,.6);background:radial-gradient(circle at 50% 40%,#b8a89a,#6b6b70)}
.quote-mark{top:128px;font-size:200px;line-height:1;color:rgba(255,255,255,.55);font-weight:900}
.testimonials .name{top:282px;left:0;width:1200px;text-align:center;color:var(--white);font-size:23px}
.testimonials .text{top:323px;left:200px;width:800px;text-align:center;color:var(--white);font-style:italic;font-size:14px;line-height:30px}

/* newsletter + footer */
.footer{top:3205px;height:409px;background:var(--footer);color:#ccc}
.newsletter{top:3150px;left:200px;width:800px;height:103px;background:var(--red)}
.newsletter .field{position:absolute;left:60px;top:28px;width:565px;height:50px;border:2px solid rgba(255,255,255,.8);border-radius:6px;color:var(--white);font-size:13px;padding:15px 20px}
.newsletter .send{position:absolute;left:682px;top:22px;width:62px;height:62px;border-radius:50%;background:var(--white);display:flex;align-items:center;justify-content:center}
.footer h6{font-size:15px;font-weight:400;color:var(--white);letter-spacing:.5px}
.links{font-size:13px;line-height:28px;color:#ddd;list-style:none}
.links li::before{content:"›";margin-right:10px;color:#aaa}
.contact{font-size:13px;line-height:22px;color:#ddd}
.map{top:168px;left:627px;width:202px;height:100px;background:linear-gradient(135deg,#e4e4e4,#c8c8c8)}
.foot-logo{top:178px;left:880px;font-size:34px;font-weight:900;color:#8a8a8a;line-height:1}
.foot-logo small{display:block;font-size:13px;letter-spacing:5px;margin-top:4px;text-align:center}
.copyright{top:287px;left:880px;font-size:13px;line-height:22px;color:#ddd}
</style>
</head>
<body>

<!-- HERO -->
<div class="section hero" role="img" aria-label="Overhead photo of a designer's desk with sketches, glasses, calculator and a red coffee cup">
  <div class="abs hero-shade"></div>
</div>

<div class="abs topbar">
  <div class="social"><span></span><span></span><span></span><span></span></div>
  <span>QUESTION CALL : 555 014 2280</span>
  <div class="right">
    <span>◍ LANGUAGES</span><span>SUPPORT</span><span>LOGIN</span>
    <span class="search-box"><svg width="12" height="12" viewBox="0 0 12 12"><circle cx="5" cy="5" r="3.5" fill="none" stroke="#fff" stroke-width="1.6"/><line x1="7.6" y1="7.6" x2="11" y2="11" stroke="#fff" stroke-width="1.6"/></svg></span>
  </div>
</div>

<div class="abs logo">RIDGEWAY<small>BANNERS</small></div>

<nav class="abs nav">
  <a class="active">HOME</a><a>ABOUT US</a><a>SERVICES</a><a>PRODUCTS</a><a>TESTIMONIALS</a><a>CONTACT US</a>
</nav>

<div class="abs cart">
  <svg width="20" height="18" viewBox="0 0 20 18"><path d="M1 2h3l2 9h10l2-7H5" fill="none" stroke="#fff" stroke-width="1.6"/><circle cx="8" cy="15" r="1.6" fill="#fff"/><circle cx="15" cy="15" r="1.6" fill="#fff"/></svg>
  <span class="count">0</span><span>MY CART</span>
</div>
<div class="abs quote-badge">FREE<br>QUOTE</div>

<div class="abs promo">
  <h2>ONE STOP SOLUTION</h2>
  <p>FOR ALL YOUR PRINTING AND SIGNAGE NEEDS<br>WITH &nbsp;MOST AFFORDABLE PRICES</p>
  <div class="btn-outline">KNOW MORE</div>
</div>
<svg class="abs" style="top:694px;left:220px" width="760" height="34" viewBox="0 0 760 34"><path d="M0 0 Q380 60 760 0 L760 6 Q380 62 0 6 Z" fill="#c9c9c9"/></svg>

<!-- ABOUT -->
<section class="section about">
  <h2 class="section-title" style="top:138px">ABOUT RIDGEWAY BANNERS</h2>
  <p class="sub">Lorem ipsum dolor sit amet, consectetuer adipiscing elit, sed diam nonummy nibh euismod tincidunt</p>
  <p class="body">Lorem ipsum dolor sit amet, consectetuer adipiscing elit, sed diam nonummy nibh euismod tincidunt ut laoreet dolore magna aliquam erat volutpat. Ut wisi enim ad minim veniam, quis nostrud exerci tation ullamcorper suscipit lobortis nisl ut aliquip ex ea commodo consequat. Duis autem vel eum iriure dolor in hendrerit in vulputate velit esse molestie consequat, vel illum dolore eu feugiat nulla facilisis at vero eros et accumsan et iusto odio dignissim qui blandit praesent luptatum zzril delenit augue duis dolore te feugait nulla facilisi.</p>
  <div class="abs btn-red" style="top:360px;left:533px;width:134px;height:40px">KNOW MORE</div>
</section>

<!-- SERVICES -->
<section class="section services">
  <h2 class="section-title" style="top:45px">OUR SERVICES</h2>
  <div class="abs service-card active" style="left:111px">
    <svg width="52" height="50" viewBox="0 0 52 50"><rect x="5" y="6" width="42" height="20" fill="none" stroke="#f26522" stroke-width="4"/><line x1="12" y1="26" x2="12" y2="46" stroke="#f26522" stroke-width="4"/><line x1="40" y1="26" x2="40" y2="46" stroke="#f26522" stroke-width="4"/><line x1="2" y1="38" x2="50" y2="38" stroke="#f26522" stroke-width="4"/><line x1="12" y1="2" x2="12" y2="6" stroke="#f26522" stroke-width="4"/><line x1="40" y1="2" x2="40" y2="6" stroke="#f26522" stroke-width="4"/></svg>
    <h3>Banner Design</h3>
    <p>Lorem ipsum dolor sit amet, consec tetuer adipiscing elit, sed diam nonu mmy nibh euismod tincidunt ut laoreet dolor sit amet, consec tetuer</p>
  </div>
  <div class="abs service-card" style="left:453px">
    <svg width="52" height="50" viewBox="0 0 52 50"><rect x="12" y="4" width="28" height="26" fill="none" stroke="#6abf2e" stroke-width="4"/><line x1="18" y1="30" x2="8" y2="48" stroke="#6abf2e" stroke-width="4"/><line x1="34" y1="30" x2="44" y2="48" stroke="#6abf2e" stroke-width="4"/></svg>
    <h3>Poster Design</h3>
    <p>Lorem ipsum dolor sit amet, consec tetuer adipiscing elit, sed diam nonu mmy nibh euismod tincidunt ut laoreet dolor sit amet, consec tetuer</p>
  </div>
  <div class="abs service-card" style="left:795px">
    <svg width="52" height="54" viewBox="0 0 52 54"><line x1="26" y1="2" x2="26" y2="52" stroke="#2a7fc1" stroke-width="4"/><path d="M8 8h32l6 6-6 6H8z" fill="none" stroke="#2a7fc1" stroke-width="4"/><path d="M44 26H12l-6 6 6 6h32z" fill="none" stroke="#2a7fc1" stroke-width="4"/></svg>
    <h3>Signage</h3>
    <p>Lorem ipsum dolor sit amet, consec tetuer adipiscing elit, sed diam nonu mmy nibh euismod tincidunt ut laoreet dolor sit amet, consec tetuer</p>
  </div>
</section>

<!-- PROJECTS -->
<section class="section projects">
  <h2 class="section-title" style="top:50px">SOME OF OUR LATEST PROJECTS</h2>
  <div class="abs filters">
    <span class="active">ALL PRODUCTS</span><span>BANNERS</span><span>POSTERS</span><span>SIGNAGE</span><span>FABRICS</span><span>STICKERS</span>
  </div>
  <div class="abs tile" style="top:202px;left:111px;width:443px;height:444px;background:linear-gradient(160deg,#7a6e62,#3d3a36 60%,#5b564f)" role="img" aria-label="Street photo of a printed pavement sign outside a row of shops">
    <div class="caption"><h4>Halcrest Doorway Banner</h4><p>Lorem ipsum dolor sit amet, consec tetuer adipiscing elit, sed diam nonu mmy nibh euismod tincidunt ut laoreet dolor sit</p></div>
  </div>
  <div class="abs tile" style="top:202px;left:590px;width:232px;height:203px;background:linear-gradient(150deg,#6f7a5e,#a9a28f)" role="img" aria-label="Photo of an outdoor poster display"><div class="plus"></div></div>
  <div class="abs tile" style="top:202px;left:855px;width:232px;height:203px;background:linear-gradient(150deg,#8a7d74,#b63a3a 60%,#6c6058)" role="img" aria-label="Photo of banners along a shopfront"><div class="plus"></div></div>
  <div class="abs tile" style="top:443px;left:590px;width:232px;height:203px;background:linear-gradient(150deg,#8d8f92,#5c6066)" role="img" aria-label="Photo of a bus shelter advertisement"><div class="plus"></div></div>
  <div class="abs tile" style="top:443px;left:855px;width:232px;height:203px;background:linear-gradient(150deg,#7d8894,#45505a)" role="img" aria-label="Photo of a street signage panel"><div class="plus"></div></div>
</section>

<!-- FEATURES -->
<section class="section features">
  <h2 class="section-title">SO, AMONG OTHER FEATURES, HERE'S A FEW OF THEM</h2>
  <div class="abs feature-card" style="left:159px">
    <svg width="56" height="56" viewBox="0 0 56 56"><path d="M28 6C14 6 6 16 6 28s9 22 20 22c4 0 5-3 3-6s0-6 4-6h7c6 0 10-4 10-10C50 15 40 6 28 6z" fill="#666"/><circle cx="18" cy="24" r="3.5" fill="#fff"/><circle cx="28" cy="16" r="3.5" fill="#fff"/><circle cx="39" cy="22" r="3.5" fill="#fff"/></svg>
    <h5>FREE DESIGN<br>SERVICE</h5>
    <p>Lorem ipsum dolor sit amet,<br>consec tetuer adipiscing</p>
  </div>
  <div class="abs feature-card" style="left:388px">
    <svg width="56" height="56" viewBox="0 0 56 56"><circle cx="28" cy="22" r="16" fill="#666"/><circle cx="28" cy="22" r="8" fill="#fff"/><path d="M18 34l-6 18 8-4 4 6 4-14zM38 34l6 18-8-4-4 6-4-14z" fill="#666"/></svg>
    <h5>ENSURE<br>QUALITY</h5>
    <p>Lorem ipsum dolor sit amet,<br>consec tetuer adipiscing</p>
  </div>
  <div class="abs feature-card" style="left:617px">
    <svg width="64" height="56" viewBox="0 0 64 56"><rect x="4" y="14" width="34" height="26" fill="#666"/><path d="M38 22h12l8 10v8H38z" fill="#666"/><circle cx="16" cy="44" r="6" fill="#666" stroke="#fff" stroke-width="2"/><circle cx="48" cy="44" r="6" fill="#666" stroke="#fff" stroke-width="2"/></svg>
    <h5>FAST<br>DELIVERY</h5>
    <p>Lorem ipsum dolor sit amet,<br>consec tetuer adipiscing</p>
  </div>
  <div class="abs feature-card" style="left:843px">
    <svg width="60" height="56" viewBox="0 0 60 56"><g fill="#666"><rect x="6" y="40" width="18" height="5"/><rect x="6" y="33" width="18" height="5"/><rect x="6" y="26" width="18" height="5"/><rect x="28" y="40" width="18" height="5"/><rect x="28" y="33" width="18" height="5"/><rect x="28" y="26" width="18" height="5"/><rect x="28" y="19" width="18" height="5"/><rect x="28" y="12" width="18" height="5"/></g><circle cx="48" cy="40" r="9" fill="#666" stroke="#fff" stroke-width="2"/></svg>
    <h5>PRICE<br>GUARANTEE</h5>
    <p>Lorem ipsum dolor sit amet,<br>consec tetuer adipiscing</p>
  </div>
</section>

<!-- TESTIMONIALS -->
<section class="section testimonials" role="img" aria-label="Blurred office background photo">
  <h2 class="section-title">HERE'S WHAT OUR CUSTOMERS SAY</h2>
  <div class="abs quote-mark" style="left:128px">“</div>
  <div class="abs quote-mark" style="left:978px">”</div>
  <div class="abs avatar" role="img" aria-label="Customer portrait photo"></div>
  <div class="abs name">Ellis Harrow</div>
  <p class="abs text">Lorem ipsum dolor sit amet, consec tetuer adipiscing elit, sed diam nonu mmy nibh euismod tincidunt ut laoreet dolor sit amet, consec tetuer &nbsp;lorem ipsum dolor sit amet, consec tetuer adipiscing elit, sed diam nonu mmy nibh euismod tincidunt ut laoreet dolor sit amet, consec tetuer</p>
</section>

<!-- FOOTER -->
<footer class="section footer">
  <h6 class="abs" style="top:128px;left:115px">QUICK LINKS</h6>
  <ul class="abs links" style="top:160px;left:115px">
    <li>Home</li><li>About Us</li><li>Services</li><li>Products</li><li>Testimonials</li><li>Contact Us</li>
  </ul>
  <ul class="abs links" style="top:160px;left:245px">
    <li>Login/Register</li><li>My Account</li><li>My Orders</li><li>Support</li><li>Privacy Policy</li><li>Sitemap</li>
  </ul>
  <h6 class="abs" style="top:128px;left:420px">CONTACT DETAILS</h6>
  <div class="abs contact" style="top:162px;left:420px">
    <div style="display:flex;gap:10px"><svg width="12" height="16" viewBox="0 0 12 16"><path d="M6 0C3 0 0 2.4 0 6c0 4 6 10 6 10s6-6 6-10C12 2.4 9 0 6 0z" fill="#ccc"/><circle cx="6" cy="6" r="2.2" fill="#353535"/></svg><div>RIDGEWAY BANNERS,<br>Lorem ipsum dolor sit amet,<br>consec tetuer adipiscing</div></div>
    <div style="display:flex;gap:10px;margin-top:14px;align-items:center"><svg width="14" height="11" viewBox="0 0 14 11"><rect x="0.5" y="0.5" width="13" height="10" fill="none" stroke="#ccc"/><path d="M0.5 0.5l6.5 6 6.5-6" fill="none" stroke="#ccc"/></svg>info@ridgewaybanners.example</div>
    <div style="display:flex;gap:10px;margin-top:16px;align-items:center;font-size:16px;font-weight:700;color:#fff"><svg width="14" height="14" viewBox="0 0 14 14"><path d="M3 0l3 3-2 2c1 2 3 4 5 5l2-2 3 3-2 3C6 14 0 8 0 3z" fill="#ccc"/></svg>555 014 2280</div>
  </div>
  <div class="abs map" role="img" aria-label="Small street map showing the office location"></div>
  <div class="abs foot-logo">RIDGEWAY<small>BANNERS</small></div>
  <div class="abs copyright">Copyright 2015 <b style="color:#fff">Ridgeway Banners</b>.<br>All Rights Reserved.</div>
</footer>

<div class="abs newsletter">
  <div class="field">ENTER YOUR EMAIL ADDRESS</div>
  <svg class="abs" style="left:620px;top:40px" width="70" height="34" viewBox="0 0 70 34"><path d="M2 18 Q20 36 36 20 Q50 6 64 16" fill="none" stroke="#fff" stroke-width="1.5" stroke-dasharray="4 4"/></svg>
  <div class="send"><svg width="28" height="26" viewBox="0 0 28 26"><path d="M1 12L27 1 20 25 13 17z" fill="#d0121b"/><path d="M13 17l14-16-10 20z" fill="#a80d14"/></svg></div>
</div>

</body>
</html>
```